Business Card Design For A Renovation Contractor Company

We need a business card for a new company based in Singapore, our company name is "RB Tolvane". We are a renovation contractor that builds designs into reality. We build more of F&B restaurants, retail stores and commercial offices. We work very closely with designers. The final design should communicate to our client that we are a company that you can trust, that will plan and complete your project without giving you a headache. I like my client to remember my company as "RB". The beauty of SIMPLE is important.

Industry/Entity Type

Contractor

Requirements
Nice to have
• Black or Red base

```html
<!DOCTYPE html>
<html lang="en">
<head>
<meta charset="utf-8">
<title>RB Tolvane – Business Card</title>
<link rel="stylesheet" href="https://fonts.googleapis.com/css2?family=Open+Sans:wght@400;600&display=swap">
<style>
  :root {
    --backdrop: #e3e7e8;
    --card-dark: #2b2828;
    --card-light: #ffffff;
    --accent-red: #e3262b;
    --text-light: #f1f1f1;
    --text-muted: #c9c9c9;
    --text-dark: #2b2828;
    --tagline-grey: #6f6f6f;
  }
  * { margin: 0; padding: 0; box-sizing: border-box; }
  html, body { width: 1200px; height: 505px; overflow: hidden; }
  body {
    background: var(--backdrop);
    font-family: "Open Sans", Arial, sans-serif;
    position: relative;
  }
  .card {
    position: absolute;
    top: 146px;
    width: 322px;
    height: 172px;
    overflow: hidden;
  }
  .card--front { left: 264px; background: var(--card-light); }
  .card--back { left: 623px; background: var(--card-dark); }

  .front-shape { position: absolute; inset: 0; }

  .brand { position: absolute; text-align: center; }
  .brand-dot {
    display: block;
    margin: 0 auto 5px;
    width: 34px; height: 34px;
    border-radius: 50%;
  }
  .brand-name {
    display: block;
    font-size: 21px;
    font-weight: 400;
    line-height: 1;
    letter-spacing: -0.3px;
  }
  .brand-tagline {
    display: inline-block;
    margin-top: 3px;
    font-size: 8px;
    line-height: 1;
    letter-spacing: 0.2px;
    border-top: 1px solid var(--accent-red);
    padding-top: 2px;
  }

  .card--front .brand { left: 12px; top: 44px; width: 130px; }
  .card--front .brand-dot { background: var(--accent-red); }
  .card--front .brand-name { color: var(--text-dark); }
  .card--front .brand-tagline { color: var(--tagline-grey); }

  .contact-block { position: absolute; left: 205px; top: 40px; }
  .person-name { color: var(--accent-red); font-size: 11px; font-weight: 400; line-height: 1.2; }
  .person-role { color: var(--text-light); font-size: 8px; line-height: 1.3; }
  .contact-list { list-style: none; margin-top: 38px; }
  .contact-list li {
    display: flex; align-items: center; gap: 5px;
    color: var(--text-light);
    font-size: 9px; line-height: 13.5px;
  }
  .contact-list svg { width: 6px; height: 6px; fill: var(--text-light); flex: none; }

  .corner-fill { position: absolute; }
  .corner-fill--top { right: 0; top: 0; width: 64px; height: 86px; }
  .corner-fill--bottom { left: 0; bottom: 0; width: 88px; height: 96px; }

  .card--back .brand { left: 0; right: 0; top: 38px; }
  .card--back .brand-dot { border: 2px solid var(--text-muted); width: 40px; height: 40px; }
  .card--back .brand-name { color: var(--text-light); font-size: 26px; }
  .card--back .brand-tagline { color: var(--text-muted); font-size: 9px; }
  .back-web { display: block; margin-top: 4px; color: var(--text-light); font-size: 9px; }
</style>
</head>
<body>

<section class="card card--front" aria-label="Business card front">
  <svg class="front-shape" viewBox="0 0 322 172" width="322" height="172" aria-hidden="true">
    <path d="M149 0 C183 42 186 128 137 172 L145 172 C193 128 190 42 156 0 Z" fill="var(--accent-red)"/>
    <path d="M160 0 C194 42 197 128 149 172 L322 172 L322 0 Z" fill="var(--card-dark)"/>
  </svg>

  <div class="brand">
    <span class="brand-dot"></span>
    <span class="brand-name">RB Tolvane</span>
    <span class="brand-tagline">plans made into solid spaces</span>
  </div>

  <div class="contact-block">
    <p class="person-name">Mara Lenk</p>
    <p class="person-role">Managing Director</p>
    <ul class="contact-list">
      <li><svg viewBox="0 0 10 10"><path d="M2 0 L4 2.5 L3 3.5 C4 5.5 4.5 6 6.5 7 L7.5 6 L10 8 L8.5 10 C4 9.5 0.5 6 0 1.5 Z"/></svg>987.654.3210</li>
      <li><svg viewBox="0 0 10 10"><rect x="1" y="3" width="8" height="5" rx="1"/><rect x="3" y="0" width="4" height="3"/><rect x="3" y="7" width="4" height="3"/></svg>987.654.3201</li>
      <li><svg viewBox="0 0 10 10"><path d="M0 2 H10 V8 H0 Z M0 2 L5 6 L10 2" stroke="var(--card-dark)" stroke-width="0.8"/></svg>info@rbtolvane.com</li>
      <li><svg viewBox="0 0 10 10"><circle cx="5" cy="5" r="5"/></svg>www.rbtolvane.com</li>
    </ul>
  </div>
</section>

<section class="card card--back" aria-label="Business card back">
  <svg class="corner-fill corner-fill--top" viewBox="0 0 64 86" width="64" height="86" role="img" aria-label="Decorative cluster of translucent grey and red hexagons">
    <defs>
      <linearGradient id="topFade" x1="0" y1="0" x2="0" y2="1">
        <stop offset="0" stop-color="#8a8686" stop-opacity="0.7"/>
        <stop offset="1" stop-color="#c8402f" stop-opacity="0.85"/>
      </linearGradient>
    </defs>
    <rect width="64" height="86" fill="url(#topFade)"/>
  </svg>
  <svg class="corner-fill corner-fill--bottom" viewBox="0 0 88 96" width="88" height="96" role="img" aria-label="Decorative cluster of translucent grey and red hexagons">
    <defs>
      <linearGradient id="bottomFade" x1="0" y1="0" x2="0" y2="1">
        <stop offset="0" stop-color="#7d7979" stop-opacity="0.55"/>
        <stop offset="1" stop-color="#c0402f" stop-opacity="0.85"/>
      </linearGradient>
    </defs>
    <rect width="88" height="96" fill="url(#bottomFade)"/>
  </svg>

  <div class="brand">
    <span class="brand-dot"></span>
    <span class="brand-name">RB Tolvane</span>
    <span class="brand-tagline">plans made into solid spaces</span>
    <span class="back-web">www.rbtolvane.com</span>
  </div>
</section>

</body>
</html>
```